Whitcombe Business Card Design

The name of the business is Dario Whitcombe, CPA LLC
The service that we offer is Accounting, Tax & Consulting Services. I need it to have the following items:
Dario Whitcombe, Principal
Phone Number
Email Address
Physical Address

I have attached the company logo, one in black and one in white. Please provide a design in black background and the other in white background. Please include "Accounting, Tax & Consulting Services". I want the business card to be clean and very professional.

```html
<!DOCTYPE html>
<html lang="en">
<head>
<meta charset="utf-8">
<title>Dario Whitcombe, CPA LLC — Business Cards</title>
<link href="https://fonts.googleapis.com/css2?family=Montserrat:wght@500;600&family=Roboto:wght@300;400&display=swap" rel="stylesheet">
<style>
  :root {
    --backdrop: #2a2a2b;
    --card-dark-top: #2c2c2e;
    --card-dark-bottom: #1d1d1f;
    --card-light-top: #f4f4f4;
    --card-light-bottom: #e4e4e4;
    --brand-red: #8e1518;
    --ink-dark: #2f2f31;
    --ink-grey: #7a7a7c;
    --ink-light: #f1f1f1;
    --ink-muted: #8d8d8f;
  }
  html, body {
    margin: 0;
    width: 1200px;
    height: 1138px;
    overflow: hidden;
    background: var(--backdrop);
  }
  .canvas { position: relative; width: 1200px; height: 1138px; }
  .card {
    position: absolute;
    left: 273px;
    width: 621px;
    height: 376px;
    border-radius: 16px;
    overflow: hidden;
  }
  .card--front {
    top: 184px;
    background: linear-gradient(160deg, var(--card-dark-top), var(--card-dark-bottom));
  }
  .card--back {
    top: 606px;
    background: linear-gradient(180deg, var(--card-light-top), var(--card-light-bottom));
  }
  .brand-square { position: absolute; }
  .card--front .brand-square {
    left: 268px; top: 112px; width: 86px; height: 86px;
    background: var(--ink-light);
  }
  .card--back .brand-square {
    left: 496px; top: 42px; width: 83px; height: 83px;
    background: var(--ink-dark);
  }
  .wordmark {
    position: absolute;
    font-family: "Montserrat", sans-serif;
    font-weight: 600;
    white-space: nowrap;
    margin: 0;
  }
  .card--front .wordmark {
    left: 0; right: 0; top: 206px;
    text-align: center;
    font-size: 26px;
    color: var(--ink-light);
  }
  .card--back .wordmark {
    left: 28px; top: 48px;
    font-size: 21px;
    color: var(--ink-dark);
  }
  .tagline {
    position: absolute;
    font-family: "Montserrat", sans-serif;
    font-weight: 500;
    letter-spacing: 2.2px;
    white-space: nowrap;
    margin: 0;
  }
  .card--front .tagline {
    left: 0; right: 0; top: 244px;
    text-align: center;
    font-size: 17px;
    color: var(--ink-muted);
  }
  .card--back .tagline {
    left: 28px; top: 80px;
    font-size: 15px;
    color: var(--ink-grey);
  }
  .person-name {
    position: absolute; left: 28px; top: 150px; margin: 0;
    font-family: "Montserrat", sans-serif; font-weight: 600;
    font-size: 20px; color: var(--brand-red); letter-spacing: .5px;
  }
  .person-role {
    position: absolute; left: 28px; top: 178px; margin: 0;
    font-family: "Roboto", sans-serif; font-weight: 300;
    font-size: 16px; color: var(--ink-dark);
  }
  .contact-list {
    position: absolute; left: 28px; top: 223px;
    margin: 0; padding: 0; list-style: none;
    font-family: "Roboto", sans-serif; font-weight: 300;
    font-size: 16px; color: var(--ink-dark);
  }
  .contact-list li { display: flex; align-items: center; height: 24px; }
  .contact-list svg { width: 14px; height: 14px; margin-right: 12px; fill: var(--brand-red); }
  .address {
    position: absolute; left: 28px; top: 302px; margin: 0;
    font-family: "Roboto", sans-serif; font-weight: 300;
    font-size: 16px; line-height: 24px; color: var(--ink-dark);
  }
  .services-band {
    position: absolute; left: 246px; right: 0; bottom: 0; height: 46px;
    background: var(--brand-red);
    clip-path: polygon(24px 0, 100% 0, 100% 100%, 0 100%);
  }
  .services-band span {
    position: absolute; right: 36px; top: 12px;
    font-family: "Roboto", sans-serif; font-weight: 300;
    font-size: 15.5px; color: #fff; white-space: nowrap;
  }
</style>
</head>
<body>
<main class="canvas">
  <section class="card card--front">
    <div class="brand-square"></div>
    <h1 class="wordmark">DARIO WHITCOMBE, CPA, LLC</h1>
    <p class="tagline">CERTIFIED PUBLIC ACCOUNTANT</p>
  </section>

  <section class="card card--back">
    <h2 class="wordmark">DARIO WHITCOMBE, CPA, LLC</h2>
    <p class="tagline">CERTIFIED PUBLIC ACCOUNTANT</p>
    <div class="brand-square"></div>

    <h3 class="person-name">DARIO WHITCOMBE</h3>
    <p class="person-role">Principal</p>

    <ul class="contact-list">
      <li><svg viewBox="0 0 16 16"><path d="M1 5c0-2 3-3 7-3s7 1 7 3v1h-4V5H5v1H1zM3 7h10l1 7H2z"/></svg>828-555-0142</li>
      <li><svg viewBox="0 0 16 16"><path d="M1 3h14v10H1zM2 4l6 5 6-5v1L8 10 2 5z" fill-rule="evenodd"/></svg>dw@dariowhitcombellc.com</li>
      <li><svg viewBox="0 0 16 16"><circle cx="8" cy="8" r="7"/><path d="M1 8h14M8 1v14M3 4h10M3 12h10" stroke="#eee" stroke-width="1" fill="none"/></svg>www.dariowhitcombellc.com</li>
    </ul>

    <p class="address">1234, Anywhere Street, Any<br>Town Name, US 123456</p>

    <div class="services-band"><span>Accounting, Tax &amp; Consulting Services</span></div>
  </section>
</main>
</body>
</html>
```